Modern card design needed for building development company

We are looking for a sharp modern new look for our business cards.
We are a New Zealand based company called TKR Ventures NZ LTD that specialises in subdividing large sections, housing and commercial buildings.
We have attached a photo of the current logo and would like to see it improved somehow as it looks a bit dated.
We are open to any colours.

Target Market(s)

Investors, Property buyers

Industry/Entity Type

Investment

Contact Information for Business Card

TKR VENTURES NZ LTD
www.tkrventuresnz.co.nz

Damon Whitcombe
Phone +64 21 938 104
Email dpwhitcombe@korumail.co.nz

Font styles to use
Serif
Sans Serif

Colors
0792cd
33a6d7
85cae6
6b449b
886aae
f04a50
ec1f27
f37122
f68d4d

Requirements
Must have
• Please try and make the logo more modern or if you have a similar one we would like to see it.

```html
<!DOCTYPE html>
<html lang="en">
<head>
<meta charset="utf-8">
<title>TKR Ventures NZ LTD – Business Card</title>
<link href="https://fonts.googleapis.com/css2?family=Open+Sans:wght@400;600;700&display=swap" rel="stylesheet">
<style>
  :root {
    --page-bg: #d9d6d2;
    --card-black: #050505;
    --card-glow: #2a2a2a;
    --accent-gold: #f0ac10;
    --text-white: #f2f2f2;
    --text-silver: #cfcfcf;
    --tab-grey: #bfbfbf;
  }
  * { box-sizing: border-box; margin: 0; padding: 0; }
  html, body {
    width: 1200px;
    height: 844px;
    overflow: hidden;
    background: var(--page-bg);
    font-family: "Open Sans", Arial, sans-serif;
  }
  .sheet {
    width: 1200px;
    height: 844px;
    display: flex;
    align-items: center;
    justify-content: center;
    gap: 44px;
  }
  .card {
    position: relative;
    width: 520px;
    height: 289px;
    background: var(--card-black);
    overflow: hidden;
    box-shadow: 0 6px 18px rgba(0,0,0,0.25);
  }

  /* Back of card: contact details */
  .card--contact::before,
  .card--contact::after {
    content: "";
    position: absolute;
    left: 0;
    right: 0;
    height: 12px;
    background: var(--accent-gold);
  }
  .card--contact::before { top: 0; }
  .card--contact::after { bottom: 0; }
  .contact {
    position: absolute;
    top: 50%;
    left: 0;
    right: 0;
    transform: translateY(-50%);
    text-align: center;
  }
  .contact__name {
    color: var(--accent-gold);
    font-weight: 700;
    font-size: 17px;
    letter-spacing: 0.5px;
    text-transform: uppercase;
    margin-bottom: 14px;
  }
  .contact__line {
    color: var(--text-white);
    font-size: 12.5px;
    line-height: 22px;
    text-transform: uppercase;
    letter-spacing: 0.3px;
  }

  /* Front of card: brand */
  .card--brand {
    background: radial-gradient(ellipse at 50% 42%, var(--card-glow) 0%, var(--card-black) 62%);
  }
  .edge-tab {
    position: absolute;
    width: 26px;
    height: 38px;
    background: var(--accent-gold);
  }
  .edge-tab::after {
    content: "";
    position: absolute;
    top: 0;
    width: 6px;
    height: 100%;
    background: var(--tab-grey);
  }
  .edge-tab--left { left: 0; top: 186px; }
  .edge-tab--left::after { right: -6px; }
  .edge-tab--right { right: 0; top: 42px; }
  .edge-tab--right::after { left: -6px; }
  .brand {
    position: absolute;
    top: 50%;
    left: 50%;
    transform: translate(-50%, -50%);
    display: flex;
    align-items: center;
    gap: 14px;
  }
  .brand__square {
    width: 22px;
    height: 22px;
    background: var(--accent-gold);
  }
  .brand__name {
    color: var(--text-silver);
    font-weight: 600;
    font-size: 22px;
    letter-spacing: 2px;
    text-transform: uppercase;
    white-space: nowrap;
  }
</style>
</head>
<body>
  <main class="sheet">
    <section class="card card--contact" aria-label="Card back">
      <div class="contact">
        <p class="contact__name">Damon Whitcombe</p>
        <p class="contact__line">+64 21 938 104</p>
        <p class="contact__line">dpwhitcombe@korumail.co.nz</p>
        <p class="contact__line">www.tkrventuresnz.co.nz</p>
      </div>
    </section>

    <section class="card card--brand" aria-label="Card front">
      <span class="edge-tab edge-tab--right"></span>
      <span class="edge-tab edge-tab--left"></span>
      <div class="brand">
        <span class="brand__square"></span>
        <span class="brand__name">TKR Ventures NZ LTD</span>
      </div>
    </section>
  </main>
</body>
</html>
```